I need a label design to go on our jars of honey. Our company is called Marrowdale Honey Co. The type of honey is called Fernlight Glen Honey. The jars are 1kg. Attached is the label size. Left hand side needs to have nutritional info... as attached. Middle section is our company name, honey type, 1kg & Whangamata, NZ. Right hand side needs to have info as per photo (raw honey etc). I would like to upload more pictures... but I’m unsure how to do this? Thanks, Carla

Target Market(s)

Honey consumers... families

Industry/Entity Type

Food Production

Colors

Designer to choose colors to be used in the design.

Requirements
Must have
• Nutritional info as per upload
• Type of honey & company name as per upload
• 1kg
• Address
Nice to have
• Similar fonts to upload.
• Possibly background image... floral or beach... very faint though.

```html
<!DOCTYPE html>
<html lang="en">
<head>
<meta charset="utf-8">
<title>Marrowdale Honey Co. – Fernlight Glen Honey Label</title>
<link href="https://fonts.googleapis.com/css2?family=Amatic+SC:wght@400&family=Barlow+Condensed:wght@400;500&family=Caveat:wght@500&family=Indie+Flower&display=swap" rel="stylesheet">
<style>
  :root {
    --backdrop: #dcdddd;
    --label-pink: #ec86b6;
    --berry: #a0235c;
    --ink-light: #ffffff;
    --cream: #fbeef4;
    --bloom-pink: #f6b3d0;
    --bloom-yellow: #f6e08a;
    --leaf-green: #9ccf7a;
  }
  * { box-sizing: border-box; margin: 0; padding: 0; }
  html, body {
    width: 1032px; height: 1200px; overflow: hidden;
    background: var(--backdrop);
  }
  .canvas { position: relative; width: 1032px; height: 1200px; }

  .label {
    position: absolute; left: 20px; top: 340px;
    width: 991px; height: 519px;
  }
  .label-shape { position: absolute; inset: 0; }

  .floral-crown {
    position: absolute; left: 326px; top: 6px; width: 343px; height: 126px;
    border-radius: 50% 50% 40% 40%;
    background:
      radial-gradient(ellipse at 45% 40%, var(--bloom-pink) 0%, rgba(246,179,208,0) 45%),
      radial-gradient(ellipse at 75% 65%, var(--bloom-yellow) 0%, rgba(246,224,138,0) 30%),
      radial-gradient(ellipse at 20% 70%, var(--leaf-green) 0%, rgba(156,207,122,0) 30%),
      radial-gradient(ellipse at 88% 75%, var(--leaf-green) 0%, rgba(156,207,122,0) 22%);
  }

  /* Left column: story */
  .story {
    position: absolute; left: 25px; top: 145px; width: 240px;
    text-align: center; color: var(--ink-light);
    font-family: "Indie Flower", cursive; font-size: 13.5px; line-height: 19px;
  }
  .story p { margin-bottom: 22px; }
  .story p.tight { margin-bottom: 4px; }

  /* Middle column: brand */
  .brand {
    position: absolute; left: 345px; top: 140px; width: 300px;
    text-align: center; color: var(--cream);
  }
  .brand-name {
    font-family: "Barlow Condensed", sans-serif; font-weight: 400;
    font-size: 30px; line-height: 34px; letter-spacing: 1px;
  }
  .honey-type {
    margin-top: 14px; color: var(--berry);
    font-family: "Caveat", cursive; font-weight: 500;
    font-size: 78px; line-height: 82px;
    margin-left: -40px; margin-right: -40px;
  }
  .honey-type span { display: block; }
  .honey-type .line-two { padding-left: 30px; }
  .weight { margin-top: 10px; font-family: "Amatic SC", sans-serif; font-size: 22px; line-height: 26px; }
  .origin { font-family: "Amatic SC", sans-serif; font-size: 22px; line-height: 28px; letter-spacing: 1px; }

  /* Right column: facts */
  .facts {
    position: absolute; left: 725px; top: 146px; width: 232px;
    color: var(--ink-light); text-align: center;
    font-family: "Barlow Condensed", sans-serif;
  }
  .facts-claim { font-size: 16px; line-height: 19px; }
  .nutrition {
    margin: 8px 0 0 8px; width: 216px; border: 2px solid var(--ink-light);
    text-align: left;
  }
  .nutrition-head { padding: 4px 6px 4px; border-bottom: 2px solid var(--ink-light); }
  .nutrition-title { font-size: 19px; line-height: 20px; font-weight: 500; }
  .nutrition-serving { font-size: 12.5px; line-height: 14px; }
  .nutrition-row {
    display: grid; grid-template-columns: 78px 68px 1fr;
    padding: 0 6px; font-size: 12.5px; line-height: 15px;
  }
  .nutrition-cols { padding-top: 6px; padding-bottom: 4px; border-bottom: 2px solid var(--ink-light); font-size: 12px; line-height: 13px; }
  .nutrition-body { padding: 8px 0 4px; }
  .facts-care { margin-top: 10px; font-size: 13.5px; line-height: 15px; }
</style>
</head>
<body>
<main class="canvas">
  <section class="label" aria-label="Fernlight Glen Honey jar label">
    <svg class="label-shape" width="991" height="519" viewBox="0 0 991 519" aria-hidden="true">
      <path d="M0 123 H275 A221 123 0 0 1 717 123 H991 V519 H0 Z" fill="var(--label-pink)"/>
    </svg>

    <div class="floral-crown" role="img" aria-label="Watercolour bouquet of pink, white and yellow flowers with green leaves"></div>

    <div class="story">
      <p>Sourced from the beautiful<br>Coromandel Peninsula</p>
      <p>Our honey comes to your raw &amp;<br>unpasteurised, ensuring it retains<br>all the natural goodness!</p>
      <p>Arohanui,<br>Tomas, Carla &amp; Boys</p>
      <p>‘Marrowdale’ –<br>all thanks to God for his<br>incredible creation!</p>
      <p class="tight">www.marrowdalehoney.co.nz</p>
      <p>27 Kowhai Lane Whangamata<br>New Zealand</p>
    </div>

    <div class="brand">
      <h1 class="brand-name">Marrowdale<br>Honey Co.</h1>
      <h2 class="honey-type"><span>Fernlight</span><span class="line-two">Glen Honey</span></h2>
      <p class="weight">1kg</p>
      <p class="origin">Whangamata N.Z.</p>
    </div>

    <div class="facts">
      <p class="facts-claim">100% New Zeland Honey<br>No Added Ingredients</p>
      <div class="nutrition">
        <div class="nutrition-head">
          <div class="nutrition-title">NUTRITIONAL INFORMATION</div>
          <div class="nutrition-serving">Serving per packages: 100<br>Serving size: 10g</div>
        </div>
        <div class="nutrition-row nutrition-cols">
          <span></span><span>Aveerage Quantity per Serving</span><span>Aveerage Quantity per 100g</span>
        </div>
        <div class="nutrition-body">
          <div class="nutrition-row"><span>Energy</span><span>134kj</span><span>134kj</span></div>
          <div class="nutrition-row"><span>Protein</span><span>0.04g</span><span>0.04g</span></div>
          <div class="nutrition-row"><span>Fat total</span><span>0g</span><span>0g</span></div>
          <div class="nutrition-row"><span>-saturated</span><span>0g</span><span>0g</span></div>
          <div class="nutrition-row"><span>Carbohydrate</span><span>7.9g</span><span>7.9.6g</span></div>
          <div class="nutrition-row"><span>-suguras</span><span>7.8g</span><span>7.8.1g</span></div>
          <div class="nutrition-row"><span>Sodium</span><span>1.2mg</span><span>1.2mg</span></div>
        </div>
      </div>
      <p class="facts-care">Store upright in a cool, dry place.<br>No refrigeration needed.<br>Not recommended for infants below<br>the age of 12 months.</p>
    </div>
  </section>
</main>
</body>
</html>
```